New Webpage for High Class Expert Witness Services Company

We are looking for a minimalist design for a webpage that just has our logo and an entry form offer to connect with one of our Liaisons.
The entry form should just ask for Name, Email, Contact Info and Description of Project.

Company Name is: The Marlowe Crest Advisory Services

Number of Pages Required

1 page

```html
<!DOCTYPE html>
<html lang="en">
<head>
<meta charset="UTF-8">
<title>The Marlowe Crest Advisory Services — Connect</title>
<link href="https://fonts.googleapis.com/css2?family=Poppins:wght@400;600;700&display=swap" rel="stylesheet">
<style>
  :root {
    --bg-light: #eef1f4;
    --bg-mid: #dfe4ea;
    --card: #ffffff;
    --ink: #121212;
    --field-border: #cfd2d6;
    --placeholder: #a9adb2;
    --icon: #9a9ea3;
  }
  * { box-sizing: border-box; margin: 0; padding: 0; }
  html, body { width: 1200px; height: 788px; overflow: hidden; }
  body {
    position: relative;
    font-family: "Poppins", sans-serif;
    color: var(--ink);
    background: var(--bg-light);
  }
  .backdrop {
    position: absolute; inset: 0;
    background:
      radial-gradient(ellipse at 20% 30%, var(--bg-mid) 0%, transparent 45%),
      radial-gradient(ellipse at 80% 70%, var(--bg-mid) 0%, transparent 50%),
      radial-gradient(ellipse at 60% 10%, #e6eaef 0%, transparent 40%),
      var(--bg-light);
  }
  .contact-card {
    position: absolute;
    left: 389px; top: 119px;
    width: 422px; height: 543px;
    background: var(--card);
    border-radius: 46px;
    border-top: 2px solid var(--ink);
    box-shadow: 0 14px 30px rgba(40, 50, 60, 0.18);
  }
  .brand {
    position: absolute;
    left: 0; right: 0; top: 36px;
    text-align: center;
    font-weight: 600;
    font-size: 14px;
    letter-spacing: 0.3px;
    line-height: 18px;
  }
  .brand-mark {
    display: inline-block;
    width: 12px; height: 12px;
    background: var(--ink);
    margin-right: 8px;
    vertical-align: -1px;
  }
  .field { position: absolute; left: 37px; width: 348px; }
  .field-label {
    display: block;
    font-size: 10px;
    font-weight: 700;
    line-height: 12px;
    margin-bottom: 5px;
    text-transform: uppercase;
  }
  .field-box {
    position: relative;
    height: 40px;
    border: 1px solid var(--field-border);
    border-radius: 6px;
    font-size: 11px;
    color: var(--placeholder);
    padding: 0 16px;
    line-height: 38px;
  }
  .field-box.is-textarea { height: 108px; }
  .field-icon {
    position: absolute;
    right: 16px; top: 13px;
    width: 12px; height: 12px;
    fill: var(--icon);
  }
  .field-name { top: 96px; }
  .field-email { top: 168px; }
  .field-contact { top: 241px; }
  .field-description { top: 313px; }
  .submit-button {
    position: absolute;
    left: 37px; top: 460px;
    width: 348px; height: 43px;
    background: var(--ink);
    border-radius: 6px;
    color: #fff;
    font-size: 11px;
    font-weight: 700;
    text-align: center;
    line-height: 43px;
    text-transform: uppercase;
  }
  .submit-icon {
    position: absolute;
    right: 16px; top: 15px;
    width: 13px; height: 13px;
    fill: #fff;
  }
</style>
</head>
<body>
  <div class="backdrop" role="img" aria-label="Pale grey galvanized metal texture background"></div>

  <main class="contact-card">
    <div class="brand"><span class="brand-mark"></span>The Marlowe Crest Advisory Services</div>

    <div class="field field-name">
      <span class="field-label">Name</span>
      <div class="field-box">Johny
        <svg class="field-icon" viewBox="0 0 12 12"><circle cx="6" cy="3.2" r="2.6"/><path d="M1.5 12c0-3 2-4.8 4.5-4.8S10.5 9 10.5 12z"/></svg>
      </div>
    </div>

    <div class="field field-email">
      <span class="field-label">Email</span>
      <div class="field-box">Johny@email.com
        <svg class="field-icon" viewBox="0 0 12 12"><path d="M0.5 2.5h11v1.2L6 7 0.5 3.7z"/><path d="M0.5 5l5.5 3.3L11.5 5v4.5h-11z"/></svg>
      </div>
    </div>

    <div class="field field-contact">
      <span class="field-label">Contact Info</span>
      <div class="field-box">+081 123456 789
        <svg class="field-icon" viewBox="0 0 12 12"><path d="M2.4 0.8l2 2.3-1 1.4c.7 1.6 2 2.9 3.6 3.6l1.4-1 2.3 2-1.3 2C5 11 1 7 .6 2.2z"/></svg>
      </div>
    </div>

    <div class="field field-description">
      <span class="field-label">Description of Project</span>
      <div class="field-box is-textarea">
        <svg class="field-icon" viewBox="0 0 12 12"><ellipse cx="7.3" cy="4.5" rx="4.2" ry="3.6"/><path d="M1 6.2a3 2.6 0 0 0 2 4.6l-.4 1.2 1.8-.9a3 2.4 0 0 0 1.4-1.4A5 4 0 0 1 2.5 5z"/></svg>
      </div>
    </div>

    <div class="submit-button">Connect with us
      <svg class="submit-icon" viewBox="0 0 12 12"><path d="M12 0L0 5.2l3.4 1.5L10 2 4.5 7.5V12l2.3-3 3 1.5z"/></svg>
    </div>
  </main>
</body>
</html>
```